BUSINESS CARD DESIGN

NAME- DALE VORSKIN
PHONE NUMER - 555- 714-9082
EMAIL- OFFICE@TRV-GROUNDMAKRZ.COM
BACK OF CARD- SPEACIALIZES IN LAND CLEARING, FORESTRY MUCLHING AND EXCAVATION

Contact Information for Business Card

NAME- DALE VORSKIN PHONE NUMER - 555- 714-9082 EMAIL- OFFICE@TRV-GROUNDMAKRZ.COM BACK OF CARD- SPEACIALIZES IN LAND CLEARING , MUCLHING AND EXCAVATION

```html
<!DOCTYPE html>
<html lang="en">
<head>
<meta charset="utf-8">
<title>Trevan Groundmakrz — Business Card</title>
<link rel="stylesheet" href="https://fonts.googleapis.com/css2?family=Montserrat:wght@600;700;800&display=swap">
<style>
  :root {
    --ink: #000000;
    --gold: #fdb913;
    --paper: #ffffff;
    --backdrop: #ffffff;
  }
  * { box-sizing: border-box; margin: 0; padding: 0; }
  html, body {
    width: 1200px; height: 1131px; overflow: hidden;
    background: var(--backdrop);
    font-family: "Montserrat", sans-serif;
  }
  .canvas { position: relative; width: 1200px; height: 1131px; }
  .card {
    position: absolute; left: 230px; width: 689px; height: 394px;
    overflow: hidden;
    box-shadow: 0 0 0 1px #eeeeee;
  }
  .card--front { top: 151px; background: var(--paper); }
  .card--back { top: 627px; background: var(--ink); }
  .front-panel { position: absolute; inset: 0; }
  .brand {
    position: absolute; display: flex; flex-direction: column; align-items: center;
    color: var(--gold); text-align: center;
  }
  .brand__dot {
    border: 3px solid var(--gold); border-radius: 50%;
  }
  .brand__name {
    font-weight: 800; text-transform: uppercase; line-height: 1.15;
  }
  .brand__phone {
    font-weight: 800; letter-spacing: 0.55em; margin-top: 8px;
    padding-top: 6px; border-top: 2px solid var(--gold);
  }
  .card--front .brand { left: 44px; top: 105px; width: 210px; }
  .card--front .brand__dot { width: 92px; height: 92px; margin-bottom: 12px; }
  .card--front .brand__name { font-size: 17px; }
  .card--front .brand__phone { font-size: 9px; }
  .card--back .brand { left: 204px; top: 73px; width: 280px; }
  .card--back .brand__dot { width: 128px; height: 128px; margin-bottom: 16px; }
  .card--back .brand__name { font-size: 23px; }
  .card--back .brand__phone { font-size: 11px; }
  .holder { position: absolute; left: 376px; top: 99px; color: var(--gold); }
  .holder__name { font-size: 33px; font-weight: 600; line-height: 1; white-space: nowrap; }
  .holder__role {
    display: inline-block; font-size: 22px; font-weight: 600; line-height: 1;
    margin-top: 8px; padding-bottom: 6px; border-bottom: 3px solid var(--gold);
  }
  .contacts { position: absolute; left: 373px; top: 227px; list-style: none; }
  .contacts li {
    display: flex; align-items: center; height: 20px; margin-bottom: 20px;
    color: var(--gold); font-size: 16px; font-weight: 700;
  }
  .contacts li:nth-child(2) { margin-bottom: 18px; }
  .contacts svg { width: 26px; height: 26px; margin-right: 17px; flex: none; }
  .tagline {
    position: absolute; left: 0; right: 0; top: 345px; text-align: center;
    color: var(--gold); font-size: 13.5px; font-weight: 700; letter-spacing: 0.06em;
  }
</style>
</head>
<body>
<main class="canvas">
  <section class="card card--front">
    <svg class="front-panel" viewBox="0 0 689 394" preserveAspectRatio="none" aria-hidden="true">
      <polygon points="0,0 380,0 262,394 0,394" fill="var(--ink)"/>
    </svg>
    <div class="brand">
      <span class="brand__dot"></span>
      <span class="brand__name">Trevan Groundmakrz LLC</span>
      <span class="brand__phone">555-714-9082</span>
    </div>
    <div class="holder">
      <p class="holder__name">DALE VORSKIN</p>
      <p class="holder__role">OWNER</p>
    </div>
    <ul class="contacts">
      <li>
        <svg viewBox="0 0 26 26" aria-hidden="true"><rect x="1" y="6" width="24" height="15" fill="var(--gold)"/><polyline points="1,6 13,15 25,6" fill="none" stroke="#fff" stroke-width="2"/></svg>
        @TRV-GROUNDMAKRZ.COM
      </li>
      <li>
        <svg viewBox="0 0 26 26" aria-hidden="true"><path d="M7 3 L11 8 L8.5 11 Q11 16 15 18.5 L18 16 L23 20 L20 24 Q12 24 6 17 Q2 11 3 6 Z" fill="none" stroke="var(--gold)" stroke-width="1.6" stroke-linejoin="round"/></svg>
        +555- 714-9082
      </li>
      <li>
        <svg viewBox="0 0 26 26" aria-hidden="true" fill="none" stroke="var(--gold)" stroke-width="1.6"><circle cx="13" cy="13" r="11"/><ellipse cx="13" cy="13" rx="5" ry="11"/><line x1="2" y1="13" x2="24" y2="13"/><line x1="4" y1="7.5" x2="22" y2="7.5"/><line x1="4" y1="18.5" x2="22" y2="18.5"/></svg>
        www.trv-groundmakrz.com
      </li>
    </ul>
  </section>

  <section class="card card--back">
    <div class="brand">
      <span class="brand__dot"></span>
      <span class="brand__name">Trevan Groundmakrz LLC</span>
      <span class="brand__phone">555-714-9082</span>
    </div>
    <p class="tagline">SPEACIALIZES IN LAND CLEARING , MUCLHING AND EXCAVATION</p>
  </section>
</main>
</body>
</html>
```